Q&J RESTORATION

I want a brochure similiar to the example i've attached.
My company name is Q&J Restoration. The website is: Q-J-Restoration.example.
The phone number is 919.555.0147.

I don't like the "yellow" being the main color of the example so I'm open to suggestions. I want something CLEAN & Simple, like our logo . This will be a bi fold brochure

```html
<!DOCTYPE html>
<html lang="en">
<head>
<meta charset="utf-8">
<title>Q&amp;J Restoration – Bi-fold Brochure</title>
<link href="https://fonts.googleapis.com/css2?family=Montserrat:ital,wght@0,400;0,500;1,700;1,800&display=swap" rel="stylesheet">
<style>
  :root{
    --brand-blue:#0a86d0;
    --deep-blue:#0b4fb3;
    --ink:#0b0b0b;
    --body-text:#2e2e2e;
    --paper:#ffffff;
    --backdrop:#d2d1d2;
    --fold-shade:#d6d8dc;
  }
  *{box-sizing:border-box;margin:0;padding:0}
  html,body{width:770px;height:1200px;overflow:hidden}
  body{background:var(--backdrop);font-family:"Montserrat",sans-serif;position:relative}

  .spread{position:absolute;left:90px;width:601px;height:464px;display:flex;background:var(--paper)}
  .spread--outside{top:110px}
  .spread--inside{top:626px}
  .panel{position:relative;width:300.5px;height:100%;overflow:hidden}
  .panel svg.panel-art{position:absolute;inset:0;width:100%;height:100%}

  .headline{position:absolute;font-style:italic;font-weight:800;line-height:1;white-space:nowrap;letter-spacing:-0.5px}
  .blue{color:var(--brand-blue)}
  .black{color:var(--ink)}

  /* Outside – back panel */
  .claim-eyebrow{right:17px;top:278px;font-size:18px}
  .claim-head{right:17px;top:300px;font-size:35px;text-align:right}
  .claim-head span{display:block;line-height:35px}
  .claim-rule{position:absolute;left:50px;top:415px;width:226px;height:2px;background:var(--ink);border-radius:1px}
  .call-row{position:absolute;left:11px;right:17px;top:428px;display:flex;align-items:baseline;justify-content:space-between}
  .call-row .phone-icon{width:14px;height:14px;align-self:center;margin-top:4px}
  .call-label{font-style:italic;font-weight:800;font-size:13px;color:var(--ink);margin-left:6px;margin-right:auto}
  .call-number{font-style:italic;font-weight:800;font-size:24px;color:var(--brand-blue);letter-spacing:-0.3px}

  /* Outside – cover panel */
  .panel--cover{background:linear-gradient(90deg,var(--fold-shade) 0%,#eef0f2 18%,var(--paper) 34%)}
  .company-name{position:absolute;left:22px;top:248px;display:flex;align-items:center;gap:6px;font-weight:500;font-size:15px;color:var(--brand-blue)}
  .company-name .mark{width:10px;height:10px;border:1.5px solid var(--brand-blue)}
  .cover-build{left:15px;top:299px;font-size:39px}
  .cover-renovate{left:15px;top:333px;font-size:46px}
  .cover-restore{left:15px;top:374px;font-size:39px}

  /* Inside – left panel */
  .damage-title{left:22px;top:21px;font-size:29px}
  .damage-title span{display:block;line-height:26px}
  .damage-sub{position:absolute;left:22px;top:79px;font-style:italic;font-weight:700;font-size:12.5px;color:var(--ink)}
  .benefit{position:absolute;left:22px}
  .benefit h3{font-style:italic;font-weight:800;font-size:11.5px;line-height:12px;color:var(--brand-blue);letter-spacing:-0.1px}
  .benefit p{margin-top:2px;font-size:7.6px;line-height:10.2px;color:var(--body-text)}
  .benefit--inspection{top:102px;width:268px}
  .benefit--settlement{top:152px;width:200px}
  .benefit--craft{top:201px;width:190px}
  .benefit--roof{top:261px;width:160px}

  /* Inside – right panel */
  .inside-build{right:26px;top:43px;font-size:36px}
  .inside-renovate{right:26px;top:78px;font-size:36px}
  .inside-restore{right:26px;top:112px;font-size:38px}
</style>
</head>
<body>

<!-- Outside spread -->
<section class="spread spread--outside">
  <div class="panel panel--back">
    <svg class="panel-art" viewBox="0 0 300 464" preserveAspectRatio="none">
      <defs>
        <linearGradient id="claimPhotoTone" x1="0" y1="0" x2="1" y2="1">
          <stop offset="0" stop-color="#2f4266"/>
          <stop offset="0.35" stop-color="#b99a86"/>
          <stop offset="0.6" stop-color="#dcd8d2"/>
          <stop offset="1" stop-color="#efeeeb"/>
        </linearGradient>
      </defs>
      <path d="M0 0 H203 C212 120 170 290 0 345 Z" fill="var(--ink)"/>
      <path d="M0 0 H201 C208 110 175 275 0 330 Z" fill="var(--brand-blue)"/>
      <path d="M0 0 H196 C200 100 165 255 0 296 Z" fill="url(#claimPhotoTone)" role="img" aria-label="Photo: a hand resting on a small model house over an insurance document"/>
    </svg>
    <p class="headline claim-eyebrow blue">INSURANCE</p>
    <h2 class="headline claim-head black">
      <span>CLAIM?</span>
      <span>WE’RE On</span>
      <span class="blue">YOUR TEAM</span>
    </h2>
    <div class="claim-rule"></div>
    <div class="call-row">
      <svg class="phone-icon" viewBox="0 0 24 24" aria-hidden="true">
        <path d="M6.6 10.8a15.1 15.1 0 0 0 6.6 6.6l2.2-2.2a1 1 0 0 1 1-.25 11.4 11.4 0 0 0 3.6.57 1 1 0 0 1 1 1V20a1 1 0 0 1-1 1A17 17 0 0 1 3 4a1 1 0 0 1 1-1h3.5a1 1 0 0 1 1 1c0 1.25.2 2.45.57 3.6a1 1 0 0 1-.25 1z" fill="var(--brand-blue)"/>
        <path d="M15 3.5a6 6 0 0 1 5.5 5.5M15 7a2.6 2.6 0 0 1 2 2" stroke="var(--brand-blue)" stroke-width="1.6" fill="none" stroke-linecap="round"/>
      </svg>
      <span class="call-label">CALL NOW!</span>
      <span class="call-number">(919) 555 0147</span>
    </div>
  </div>

  <div class="panel panel--cover">
    <svg class="panel-art" viewBox="0 0 300 464" preserveAspectRatio="none">
      <defs>
        <linearGradient id="stairPhotoTone" x1="0" y1="0" x2="0.4" y2="1">
          <stop offset="0" stop-color="#c9d1de"/>
          <stop offset="0.45" stop-color="#c9a66e"/>
          <stop offset="0.75" stop-color="#6d5c44"/>
          <stop offset="1" stop-color="#2d2a26"/>
        </linearGradient>
      </defs>
      <path d="M30 0 C0 70 10 170 120 232 C190 272 260 302 301 330 V0 Z" fill="var(--ink)"/>
      <path d="M27 0 C-3 70 4 152 110 212 C190 252 260 282 301 308 V0 Z" fill="var(--brand-blue)"/>
      <path d="M40 0 C15 60 30 140 130 190 C200 225 260 245 301 260 V0 Z" fill="url(#stairPhotoTone)" role="img" aria-label="Photo: a modern staircase in a flooded hallway"/>
    </svg>
    <div class="company-name"><span class="mark"></span>Q&amp;J Restoration</div>
    <h1>
      <span class="headline cover-build black">BUILD</span>
      <span class="headline cover-renovate blue">RENOVATE</span>
      <span class="headline cover-restore black">RESTORE</span>
    </h1>
  </div>
</section>

<!-- Inside spread -->
<section class="spread spread--inside">
  <div class="panel panel--benefits">
    <svg class="panel-art" viewBox="0 0 300 464" preserveAspectRatio="none">
      <defs>
        <linearGradient id="sketchTone" x1="0" y1="0" x2="0" y2="1">
          <stop offset="0" stop-color="#ffffff"/>
          <stop offset="1" stop-color="#e4e6ea"/>
        </linearGradient>
        <linearGradient id="blueprintTone" x1="0" y1="0" x2="1" y2="1">
          <stop offset="0" stop-color="#eaf2fb"/>
          <stop offset="0.5" stop-color="#b8d3f0"/>
          <stop offset="1" stop-color="#7fa9de"/>
        </linearGradient>
        <radialGradient id="wireframeTone" cx="0.5" cy="0.45" r="0.6">
          <stop offset="0" stop-color="#3d7fe0"/>
          <stop offset="1" stop-color="#0a3fa6"/>
        </radialGradient>
      </defs>
      <g role="img" aria-label="Line drawing of a house elevation">
        <circle cx="55" cy="430" r="75" fill="url(#sketchTone)" stroke="var(--brand-blue)" stroke-width="3"/>
      </g>
      <g role="img" aria-label="Photo: rolled architectural blueprints">
        <circle cx="240" cy="440" r="139" fill="url(#blueprintTone)" stroke="var(--brand-blue)" stroke-width="4"/>
      </g>
      <g role="img" aria-label="Blue wireframe rendering of a house">
        <circle cx="257" cy="303" r="44" fill="url(#wireframeTone)" stroke="var(--brand-blue)" stroke-width="4"/>
      </g>
    </svg>

    <h2 class="headline damage-title blue"><span>WATER OR MOLD</span><span>DAMAGE?</span></h2>
    <p class="damage-sub">What Happens After The Cleanup?</p>

    <div class="benefit benefit--inspection">
      <h3>ADJUSTER’S INSPECTION</h3>
      <p>Feel Confident. Be sure you received a fair and accurate assessment &amp; repair of all damages with our team’s use of industry leading estimating systems and On-Site Review.</p>
    </div>
    <div class="benefit benefit--settlement">
      <h3>TIMELY SETTLEMENT</h3>
      <p>Don’t wait. Minimize the hassle of long processing times from estimate to settlement when you team up with an insurance Repair Specialist.</p>
    </div>
    <div class="benefit benefit--craft">
      <h3>SUPERIOR CRAFTSMANSHIP</h3>
      <p>Don’t settle for satisfactory. Our team is committed to the highest standards of excellence every step of the way. Trust us when we say that we’ll make your smile</p>
    </div>
    <div class="benefit benefit--roof">
      <h3>UNDER ONE ROOF</h3>
      <p>Don’t worry. You won’t need to arrange meetings with multiple contractors we’ll take care of everything from demo to final cleanup.</p>
    </div>
  </div>

  <div class="panel panel--worksite">
    <svg class="panel-art" viewBox="0 0 300 464" preserveAspectRatio="none">
      <defs>
        <linearGradient id="worksiteTone" x1="0" y1="0" x2="0" y2="1">
          <stop offset="0" stop-color="#e4e5e8"/>
          <stop offset="0.45" stop-color="#dcdfe4"/>
          <stop offset="0.7" stop-color="#b9c6d8"/>
          <stop offset="1" stop-color="#d9dce0"/>
        </linearGradient>
      </defs>
      <rect width="300" height="464" fill="url(#worksiteTone)" role="img" aria-label="Photo: a worker in a hard hat surveying a gutted room under renovation"/>
    </svg>
    <h2>
      <span class="headline inside-build blue">BUILD</span>
      <span class="headline inside-renovate black">RENOVATE</span>
      <span class="headline inside-restore blue">RESTORE</span>
    </h2>
  </div>
</section>

</body>
</html>
```